Website Design for a holiday home letting busines

We require a redesign of our present website www.pinebrookstays.com. We want the website to stand out and look professional and clean to make holiday hunters want to book a caravan or lodge holiday with us. Our logo is red however we DO NOT want the website to be red. We want a natural colour scheme.

The final design should communicate that we are a professional company to book with.

On the home page we require;
Overview of company
Photo
Search box for holiday (check in)
Late Deals
Reviews
News

We would like the following pages designed; home page, available dates page, caravans page, content page.

The website should be responsive for smart phones. One website I do like is http://www.verdoliso.be/nl/

Target Market(s)

Families

Industry/Entity Type

Travel

Number of Pages Required

5+ page

Font styles to use
Serif

Requirements
Must have
• The project must be responsive for mobile phones and tablets.
• Ability to search for holiday home holidays
• We want a natural colour scheme.
Nice to have
• A style we like is http://www.verdoliso.be/nl/
Should not have
• Do not use red as a colour for the website. Our logo is red so this is the only time we want this used.

```html
<!DOCTYPE html>
<html lang="en">
<head>
<meta charset="utf-8">
<title>Pinebrook Stays – Private Holiday Rentals</title>
<link href="https://fonts.googleapis.com/css2?family=Cinzel:wght@400;600&family=Open+Sans:wght@300;400;600&display=swap" rel="stylesheet">
<style>
:root{
  --teal:#6cc9cc;
  --teal-light:#a9e2e2;
  --teal-pale:#d6f1f0;
  --teal-dark:#3e9fa4;
  --teal-deep:#2f7f84;
  --ink:#3c4a4d;
  --grey:#7b8a8c;
  --white:#ffffff;
  --charcoal:#3a3f40;
  --sand:#e9c98f;
  --sea:#3aa7c9;
}
*{box-sizing:border-box;margin:0;padding:0}
html,body{width:1200px;height:2948px;overflow:hidden}
body{font-family:"Open Sans",Arial,sans-serif;color:var(--white);
  background:linear-gradient(180deg,var(--teal) 0%,var(--teal-light) 30%,var(--teal-pale) 48%,var(--teal-light) 62%,var(--teal) 100%);position:relative}
.wrap{width:1000px;margin:0 auto;position:relative}

/* header */
.site-header{height:80px;background:var(--white);position:relative}
.brand{position:absolute;left:100px;top:20px;display:flex;align-items:center;gap:10px}
.brand-dot{width:34px;height:34px;border-radius:50%;background:var(--teal-dark)}
.brand-name{font-family:"Open Sans",sans-serif;font-size:22px;font-weight:600;color:var(--teal-deep)}
.main-nav{position:absolute;left:470px;top:32px;display:flex;gap:26px;font-size:11px;color:var(--grey);letter-spacing:.5px}
.main-nav .active{color:var(--teal-dark);border-bottom:2px solid var(--teal-dark);padding-bottom:6px}
.top-nav{position:absolute;right:100px;top:12px;display:flex;gap:18px;font-size:10px;color:var(--grey)}

/* hero */
.hero{height:540px;position:relative}
.hero-title{position:absolute;left:100px;top:158px;font-family:"Cinzel",serif;font-size:31px;font-weight:400;letter-spacing:1px}
.hero-text{position:absolute;left:100px;top:208px;width:330px;font-size:15px;line-height:22px;opacity:.95}
.hero-icons{position:absolute;left:100px;top:268px;display:flex;gap:8px}
.hero-icons span{width:20px;height:20px;border-radius:50%;background:var(--white);opacity:.8}
.btn{display:inline-block;background:var(--charcoal);color:var(--white);font-size:11px;letter-spacing:1px;padding:12px 16px;border-radius:3px}
.hero .btn{position:absolute;left:100px;top:318px}
.circle{position:absolute;border-radius:50%;border:6px solid var(--white)}
.circle-family{left:700px;top:165px;width:190px;height:190px;background:radial-gradient(circle at 50% 35%,#9ad6f2,#5ea3c7 55%,#7bb86a 75%)}
.circle-beach{left:820px;top:80px;width:250px;height:250px;background:linear-gradient(180deg,#5fb7e5 0%,#f2b86a 45%,#e0855a 60%,#2d8fa8 100%)}

/* feature row */
.features{height:240px;position:relative}
.media{position:absolute;top:0;height:170px;border:5px solid var(--white)}
.media-video{left:100px;width:320px;background:linear-gradient(135deg,#4e8fb2,#d8ad6b 60%,#2b6f8c)}
.media-photo{left:440px;width:320px;background:linear-gradient(180deg,#f6d27a,#e58c4d 55%,#6f5b4a)}
.video-bar{position:absolute;left:0;right:0;top:0;height:24px;background:rgba(0,0,0,.45);font-size:10px;padding:6px 8px}
.play{position:absolute;left:130px;top:60px}
.search-box{position:absolute;left:780px;top:0;width:320px;height:170px;background:var(--teal-dark);padding:18px 20px}
.field{background:var(--white);color:var(--grey);font-size:10px;height:26px;padding:7px 9px;border-radius:2px;margin-bottom:10px;display:flex;justify-content:space-between}
.field-row{display:flex;gap:10px}
.field-row .field{flex:1}
.search-box .btn{padding:8px 14px;font-size:10px}
.feature-band{position:absolute;left:100px;top:176px;width:1000px;height:64px;background:var(--teal-dark);display:flex;box-shadow:0 8px 12px rgba(0,0,0,.12)}
.feature-band div{flex:1;text-align:center;font-size:15px;line-height:64px;border-right:1px solid rgba(255,255,255,.35)}
.feature-band div:last-child{border:none}

/* sections */
.section{position:relative}
.section-head{display:flex;justify-content:space-between;align-items:center;border-bottom:1px solid rgba(255,255,255,.6);padding-bottom:10px;margin-bottom:28px}
.section-head h2{font-weight:300;font-size:30px}
.arrows{font-size:14px;letter-spacing:6px}
.cards{display:flex;gap:35px}
.card{width:310px}
.card-img{height:190px;border:5px solid var(--white)}
.card h3{font-weight:300;font-size:24px;margin-top:10px}
.card-meta{display:flex;justify-content:space-between;font-size:10px;opacity:.9;margin-top:2px}
.card .more{font-size:18px;font-weight:300;margin-top:4px}
.price{font-size:20px;font-weight:300;margin-top:6px}
.img-lounge{background:linear-gradient(135deg,#c9a889,#8b6a52 50%,#e9dccb)}
.img-kitchen{background:linear-gradient(135deg,#d9cbb7,#7e6a58 55%,#b8a38b)}
.img-bedroom{background:linear-gradient(135deg,#efe7dc,#b39b84 60%,#f4efe8)}
.img-beach{background:linear-gradient(180deg,#6fc3ea 0%,#bfe5ef 45%,#f1dfb1 70%,#e6cf97 100%)}
.img-pool{background:linear-gradient(180deg,#a9d7ef,#4a6e7f 50%,#3fb1c9)}
.img-resort{background:linear-gradient(180deg,#6cbde6,#9bbf6a 50%,#35a6c7)}

.caravans{margin-top:80px;height:380px}
.deals{margin-top:60px;height:340px}
.reviews{margin-top:60px;height:230px}
.review{display:flex;gap:28px;align-items:flex-start}
.avatar{width:110px;height:110px;border-radius:50%;border:5px solid var(--white);background:radial-gradient(circle,#d6b493,#8f6f55);flex:none}
.review h3{font-weight:300;font-size:26px}
.review small{display:block;font-size:10px;opacity:.85;margin:2px 0 10px}
.review p{font-size:11px;line-height:17px;width:820px;opacity:.95}

/* overview band */
.overview{height:400px;background:var(--teal-dark);margin-top:30px;padding-top:34px}
.overview .wrap{display:flex;gap:50px}
.company{width:600px}
.news{width:350px}
.overview h2{font-weight:300;font-size:26px;border-bottom:1px solid rgba(255,255,255,.5);padding-bottom:10px;margin-bottom:18px;display:flex;justify-content:space-between;align-items:baseline}
.overview h2 small{font-size:10px}
.lead{font-size:14px;font-weight:600;line-height:21px;margin-bottom:14px}
.company p{font-size:11px;line-height:17px;margin-bottom:12px;opacity:.95}
.news-item{display:flex;gap:14px;margin-bottom:22px}
.news-thumb{width:60px;height:60px;border-radius:50%;border:3px solid var(--white);flex:none}
.thumb-fireworks{background:radial-gradient(circle,#f5c46a,#5b3f7a 60%,#1d2540)}
.thumb-show{background:radial-gradient(circle,#8fd0f0,#2a5f88 60%,#1a2b45)}
.news-item h4{font-size:14px;font-weight:400}
.news-item small{font-size:9px;opacity:.85}
.news-item p{font-size:10px;line-height:15px;opacity:.95}

/* footer */
.site-footer{height:470px;padding-top:46px}
.site-footer .wrap{display:flex;gap:40px}
.site-footer h2{font-weight:300;font-size:30px;color:var(--ink);border-bottom:1px solid rgba(60,74,77,.3);padding-bottom:10px;margin-bottom:18px}
.col{width:306px;color:var(--ink);font-size:11px;line-height:19px}
.links{display:grid;grid-template-columns:1fr 1fr}
.input{background:var(--white);height:28px;width:180px;margin:14px 0 10px;border-radius:2px;font-size:10px;color:var(--grey);padding:6px 8px}
.col .btn{padding:7px 12px;font-size:10px}
.bottom-bar{position:absolute;left:0;top:2800px;width:1200px;height:148px;background:var(--charcoal);font-size:10px;color:#cfd6d7}
.bottom-bar .copy{position:absolute;left:100px;top:20px}
.live-chat{position:absolute;right:100px;top:-38px;background:var(--teal-dark);color:var(--white);font-size:14px;padding:10px 22px;border-radius:3px 3px 0 0}
</style>
</head>
<body>

<header class="site-header">
  <div class="brand"><span class="brand-dot"></span><span class="brand-name">Pinebrook Stays</span></div>
  <nav class="top-nav"><span>ABOUT</span><span>REVIEWS</span><span>CONTACT US</span></nav>
  <nav class="main-nav">
    <span class="active">HOME</span><span>CARAVANS &amp; LODGES</span><span>FIREWORKS TEAM</span><span>ALDERWICK CASTLE</span><span>LOCAL ATTRACTIONS</span>
  </nav>
</header>

<section class="hero">
  <h1 class="hero-title">PRIVATE HOLIDAY RENTALS</h1>
  <p class="hero-text">Quality Lodge &amp; Caravan hire at Alderwick Castle Holiday Park. Book online today!</p>
  <div class="hero-icons"><span></span><span></span></div>
  <a class="btn">MORE DETAILS</a>
  <div class="circle circle-beach" role="img" aria-label="Beach at sunset with palm trees"></div>
  <div class="circle circle-family" role="img" aria-label="Family playing together outdoors"></div>
</section>

<section class="features">
  <div class="media media-video" role="img" aria-label="Holiday park video preview">
    <div class="video-bar">Private Lodges and Caravans hire at Alderwick Castle</div>
    <svg class="play" width="50" height="36" viewBox="0 0 50 36"><rect width="50" height="36" rx="8" fill="#2b2b2b" opacity=".85"/><path d="M20 10 L33 18 L20 26Z" fill="#fff"/></svg>
  </div>
  <div class="media media-photo" role="img" aria-label="Friends jumping on the beach at sunset"></div>
  <form class="search-box">
    <div class="field"><span>Location</span><span>▾</span></div>
    <div class="field-row">
      <div class="field"><span>Check in</span><span>▾</span></div>
      <div class="field"><span>Check out</span><span>▾</span></div>
    </div>
    <a class="btn">Find Now</a>
  </form>
  <div class="feature-band"><div>No deposit holidays</div><div>Photo</div><div>Serch Holiday</div></div>
</section>

<section class="section caravans wrap">
  <div class="section-head"><h2>Caravans and Lodges</h2><span class="arrows">‹ ›</span></div>
  <div class="cards">
    <article class="card"><div class="card-img img-lounge" role="img" aria-label="Lodge lounge interior"></div><h3>New Harbour</h3><div class="card-meta"><span>Luxury Lodge</span><span>Sleeps 6</span></div><p class="more">More details</p></article>
    <article class="card"><div class="card-img img-kitchen" role="img" aria-label="Caravan kitchen and dining area"></div><h3>New Harbour</h3><div class="card-meta"><span>Luxury Lodge</span><span>Sleeps 6</span></div><p class="more">More details</p></article>
    <article class="card"><div class="card-img img-bedroom" role="img" aria-label="Lodge bedroom"></div><h3>New Harbour</h3><div class="card-meta"><span>Luxury Lodge</span><span>Sleeps 6</span></div><p class="more">More details</p></article>
  </div>
</section>

<section class="section deals wrap">
  <div class="section-head"><h2>Latest Deals</h2><span class="arrows">‹ ›</span></div>
  <div class="cards">
    <article class="card"><div class="card-img img-beach" role="img" aria-label="Sunny beach with palm tree"></div><h3>The Seabreeze</h3><div class="card-meta"><span>Fri 14th Aug - Mon 17th Aug</span><span>3 nights</span></div><p class="price">£149.00</p></article>
    <article class="card"><div class="card-img img-pool" role="img" aria-label="Caravan terrace overlooking the sea"></div><h3>The Ashford</h3><div class="card-meta"><span>Fri 21st Aug - Mon 24th Aug</span><span>3 nights</span></div><p class="price">£149.00</p></article>
    <article class="card"><div class="card-img img-resort" role="img" aria-label="Holiday park pool with palms"></div><h3>The Seabreeze</h3><div class="card-meta"><span>Fri 28th Aug - Mon 31st Aug</span><span>3 nights</span></div><p class="price">£149.00</p></article>
  </div>
</section>

<section class="section reviews wrap">
  <div class="section-head"><h2>Latest Reviews</h2><span class="arrows">‹ ›</span></div>
  <div class="review">
    <div class="avatar" role="img" aria-label="Reviewer portrait"></div>
    <div>
      <h3>“Helen Marsh”</h3>
      <small>Stayed in the New Harbour lodge, July</small>
      <p>We had a wonderful week at the park. The lodge was spotless, warm and had everything we needed for the children. Booking was easy and the team were friendly and quick to answer every question. We will certainly be back next summer.</p>
    </div>
  </div>
</section>

<section class="overview">
  <div class="wrap">
    <div class="company">
      <h2>Company Overview</h2>
      <p class="lead">Would you like to book a 2016 caravan or lodge holiday at Alderwick Castle Holiday Park and PAY NO DEPOSIT?</p>
      <p>At Pinebrook Stays we provide well-kept private caravans and lodges across the park, all checked before every arrival so your family can settle in straight away and enjoy the break.</p>
      <p>Once you add to the basket, simply choose your dates and pay the balance up to two weeks before you travel. There is no deposit to find and no hidden fees, just a clear price for your stay.</p>
    </div>
    <div class="news">
      <h2>Latest News <small>More News</small></h2>
      <div class="news-item"><div class="news-thumb thumb-fireworks" role="img" aria-label="Fireworks in night sky"></div><div><h4>Fireworks Weekend</h4><small>14 August 2015</small><p>Enjoy the Alderwick Castle fireworks display with free entry for guests staying this weekend…</p></div></div>
      <div class="news-item"><div class="news-thumb thumb-show" role="img" aria-label="Stage show with lights"></div><div><h4>Summer Show Live Alderwick Castle</h4><small>20 August 2015</small><p>Enjoy the live stage show at the park with music and entertainment for the family…</p></div></div>
    </div>
  </div>
</section>

<footer class="site-footer">
  <div class="wrap">
    <div class="col">
      <h2>Quick Links</h2>
      <div class="links"><span>Home</span><span>Fireworks Team</span><span>Rates</span><span>Alderwick Castle</span><span>Reviews</span><span>Local Attractions</span><span>Caravans &amp; Lodges</span><span></span><span>2016 Holidays</span><span></span><span>2015 Holidays</span></div>
    </div>
    <div class="col">
      <h2>Newsletter Signup</h2>
      <p>Get updates from our website or shop through our newsletter list.</p>
      <div class="input">Email</div>
      <a class="btn">submit</a>
    </div>
    <div class="col">
      <h2>Contact Us</h2>
      <p>Pinebrook Stays Ltd<br>Unit 4, Alder Court, Wickham Road<br>Northshire NE21 4PB</p>
      <p style="margin-top:10px">Telephone: 01632 960 214 Mobile: 07700 900 318<br>Email: hello@pinebrookstays.com</p>
    </div>
  </div>
</footer>

<div class="bottom-bar">
  <span class="live-chat">Live Chat</span>
  <span class="copy">© 2015 www.pinebrookstays.com. All rights reserved.</span>
</div>

</body>
</html>
```